Web Design for Two by Two Organic Soap Company

We need a website design for the company Brevin Organics based on the package design per attached.

The design should communicate high end, luxury organic. The site will provide facts about how the spread of disease causes deaths and can be prevented with hand washing. The site will also have a page about why we are passionate about organics and how that relates to our skin including skin facts.
Also, the site should have an e-commerce product page and shopping cart.

Target Market(s)

Educated, health conscious and socially conscious consumers who shop luxury. Target vendors include Marlow Grocers and Tavelli..

Industry/Entity Type

E-Commerce

Font styles to use
Other font styles liked:
• See attached

Requirements
Must have
• Use of Ying Yang leaf Logo provided.
Based on design provided.

```html
<!DOCTYPE html>
<html lang="en">
<head>
<meta charset="utf-8">
<title>Brevin Organics – Organic Soap</title>
<link href="https://fonts.googleapis.com/css2?family=Montserrat:wght@400;500;600&family=Open+Sans:wght@400;600;700&display=swap" rel="stylesheet">
<style>
:root{
  --ink:#2b2420;
  --text:#4a4440;
  --accent-red:#b3321f;
  --tan:#c9a98a;
  --logo-bg:#c8aa88;
  --logo-dark:#3a2a20;
  --plum:#8c2f6e;
  --rule:#cfcfcf;
  --footer-bg:#ececec;
  --subscribe:#3b2a1e;
  --social:#3b5998;
  --social-alt:#4a90d0;
}
*{box-sizing:border-box;margin:0;padding:0}
html,body{width:1031px;height:1200px;overflow:hidden;background:#fff}
body{font-family:"Open Sans",Arial,sans-serif;color:var(--text)}
.page{position:relative;width:1000px;height:1163px;transform:scale(1.031);transform-origin:0 0}
.abs{position:absolute}
.heading{font-family:"Montserrat",Arial,sans-serif;color:var(--ink);font-weight:400}

/* header */
.logo{left:117px;top:12px;width:179px;height:64px;background:var(--logo-bg);display:flex;align-items:center;gap:10px;padding:0 10px}
.logo-mark{width:32px;height:32px;background:var(--accent-red);flex:none}
.logo-name{font-family:"Montserrat",Arial,sans-serif;font-size:15px;font-weight:500;color:var(--logo-dark);line-height:19px}
.bag{right:117px;top:13px;font-size:11px;color:var(--ink);display:flex;align-items:center;gap:8px}
.bag strong{font-weight:700}
.bag-rule{left:665px;top:33px;width:218px;height:1px;background:var(--rule)}
.welcome-user{right:117px;top:38px;font-size:11px;color:var(--ink)}
.welcome-user b{font-weight:700}

/* nav */
.nav{left:117px;top:85px;width:766px;height:31px;border-top:2px solid #d8d8d8;border-bottom:2px solid #d8d8d8;display:flex;justify-content:center;align-items:center;gap:23px;font-family:"Montserrat",Arial,sans-serif;font-size:12px;font-weight:500;color:var(--ink);list-style:none}
.nav .current{color:var(--accent-red)}

/* hero */
.hero{left:117px;top:123px;width:766px;height:313px;overflow:hidden;background:
  radial-gradient(ellipse 200px 140px at 160px 160px,#e9e4d4 0%,rgba(233,228,212,0) 70%),
  radial-gradient(ellipse 220px 200px at 440px 150px,#c583bd 0%,rgba(197,131,189,0) 75%),
  linear-gradient(90deg,#d3d3d5 0%,#c9b6cc 40%,#b48fb0 60%,#9aae74 85%,#8fae5a 100%)}
.hero-title{left:379px;top:228px;width:490px;font-family:"Montserrat",Arial,sans-serif;font-weight:400;font-size:32px;line-height:34px;color:#fff;white-space:nowrap}
.hero-btn{left:387px;top:393px;width:84px;height:27px;background:var(--plum);color:#fff;font-family:"Montserrat",Arial,sans-serif;font-size:11.5px;font-weight:500;display:flex;align-items:center;justify-content:center}
.dots{left:834px;top:420px;display:flex;gap:3px}
.dots span{width:10px;height:10px;border-radius:50%;background:#fff}
.dots .on{background:#2a1a14}

/* intro */
.intro-title{left:117px;top:470px;font-size:20px}
.intro-text{left:117px;top:506px;width:466px;font-size:11.3px;line-height:16.3px;color:var(--text)}
.intro-photo{left:580px;top:483px;width:303px;height:95px;background:linear-gradient(90deg,#6f6a3a,#9a8f55 45%,#c9a27e 75%,#e6d1bc);clip-path:polygon(58px 0,100% 0,100% 100%,0 100%)}

/* products */
.products-title{left:117px;top:617px;font-size:20px}
.products-rule{left:250px;top:629px;width:597px;height:1px;background:var(--rule)}
.product{top:653px;width:182px}
.product-photo{width:182px;height:182px}
.product-name{margin-top:10px;font-size:12px;font-weight:700;color:var(--ink)}
.product-row{margin-top:16px;display:flex;justify-content:space-between;align-items:center}
.price{font-family:"Montserrat",Arial,sans-serif;font-size:15px;font-weight:500;color:var(--ink)}
.shop{width:88px;height:22px;background:var(--tan);color:var(--ink);font-family:"Montserrat",Arial,sans-serif;font-size:11.5px;font-weight:500;display:flex;align-items:center;justify-content:center}

/* footer */
.footer{left:0;top:938px;width:1000px;height:185px;background:var(--footer-bg)}
.news-label{left:117px;top:959px;font-family:"Montserrat",Arial,sans-serif;font-size:13px;color:var(--ink);font-weight:500}
.email{left:252px;top:955px;width:148px;height:24px;border:1px solid #d0d0d0;background:#fff;font-size:11px;color:#aaa;padding:4px 7px}
.subscribe{left:399px;top:955px;width:85px;height:24px;background:var(--subscribe);color:#fff;font-size:12px;display:flex;align-items:center;justify-content:center}
.social{top:955px;display:flex;align-items:center;gap:8px;font-family:"Montserrat",Arial,sans-serif;font-size:13px;font-weight:500;color:var(--ink);white-space:nowrap}
.social i{display:block;width:23px;height:23px;background:var(--social)}
.col{top:1009px;font-size:11.5px;color:var(--ink)}
.col h4{font-family:"Montserrat",Arial,sans-serif;font-size:13px;font-weight:500;margin-bottom:9px}
.col ul{list-style:none;display:flex;gap:0}
.col li{line-height:19.7px}
.cards{right:117px;top:1040px;display:flex;gap:2px}
.cards span{width:28px;height:18px;border:1px solid #bbb;background:#fff;font-size:6px;display:flex;align-items:center;justify-content:center;color:var(--ink)}
.copy{left:117px;top:1137px;font-size:11px;color:var(--ink)}
.legal{right:117px;top:1137px;font-size:11px;color:var(--ink)}
</style>
</head>
<body>
<div class="page">
  <header>
    <div class="abs logo"><span class="logo-mark"></span><span class="logo-name">Brevin Organics</span></div>
    <div class="abs bag">
      <svg width="13" height="13" viewBox="0 0 13 13"><path d="M1 4h11v9H1z" fill="#2b2420"/><path d="M4 4V2.5a2.5 2.5 0 0 1 5 0V4" stroke="#2b2420" stroke-width="1.3" fill="none"/></svg>
      <strong>MY BAG</strong>&nbsp; 0 item(s): $0.00
    </div>
    <div class="abs bag-rule"></div>
    <div class="abs welcome-user">Welcome to brevin organics, <b>Login</b> or <b>Register</b></div>
    <ul class="abs nav">
      <li class="current">HOME</li><li>SOAPS</li><li>BODY BUTTER</li><li>TWO BY TWO</li><li>SKIN FACTS</li><li>ABOUT</li><li>CONTACT</li>
    </ul>
  </header>

  <section>
    <div class="abs hero" role="img" aria-label="Stack of handmade organic soap bars on red stones before a soft purple flower background"></div>
    <h1 class="abs hero-title">Lorem ipsum dolor sit amet,<br>consectetur adipisi</h1>
    <div class="abs hero-btn">SHOP NOW</div>
    <div class="abs dots"><span class="on"></span><span></span><span></span><span></span></div>
  </section>

  <section>
    <h2 class="abs heading intro-title">Welcome to Brevin Organics</h2>
    <p class="abs intro-text">Sed ut perspiciatis unde omnis iste natus error sit voluptatem accusantium dolorem-que laudantium, totam rem aperiam, eaque ipsa quae ab illo inventore veritatis et quasi architecto beatae vitae dicta sunt explicabo. Nemo enim ipsam voluptatem quia voluptas sit aspernatur aut odit aut fugit, sed quia consequuntur magni dolores eos qui ratione voluptatem sequi</p>
    <svg class="abs" style="left:570px;top:474px" width="72" height="112"><line x1="70" y1="1" x2="1" y2="110" stroke="#d8d8d8" stroke-width="1"/></svg>
    <div class="abs intro-photo" role="img" aria-label="Hands holding freshly picked green and dark olives"></div>
  </section>

  <section>
    <h2 class="abs heading products-title">Our Product</h2>
    <div class="abs products-rule"></div>
    <svg class="abs" style="left:852px;top:622px" width="32" height="15"><circle cx="7" cy="7.5" r="6" fill="#fff" stroke="#bbb"/><path d="M8.5 5l-2.5 2.5 2.5 2.5" stroke="#666" fill="none"/><circle cx="24" cy="7.5" r="6" fill="#fff" stroke="#bbb"/><path d="M22.5 5l2.5 2.5-2.5 2.5" stroke="#666" fill="none"/></svg>

    <article class="abs product" style="left:117px">
      <div class="product-photo" role="img" aria-label="Lavender and green soap bars on weathered wood" style="background:linear-gradient(135deg,#6d7a5a,#9c8fc4 45%,#8a8a7a 80%,#5d5a4e)"></div>
      <div class="product-name">Patchouli</div>
      <div class="product-row"><span class="price">$12.00</span><span class="shop">SHOP NOW</span></div>
    </article>
    <article class="abs product" style="left:312px">
      <div class="product-photo" role="img" aria-label="Pale soap bars, candle and spray bottles in soft light" style="background:linear-gradient(160deg,#e4ddd2,#f1ece4 50%,#e8e2d8)"></div>
      <div class="product-name">Lemongrass</div>
      <div class="product-row"><span class="price">$12.00</span><span class="shop">SHOP NOW</span></div>
    </article>
    <article class="abs product" style="left:507px">
      <div class="product-photo" role="img" aria-label="Cream soap bar with brush and glass bottle" style="background:linear-gradient(150deg,#c9c29a,#e9e3d4 40%,#d8cbb2 75%,#b59a72)"></div>
      <div class="product-name">Sandalwood</div>
      <div class="product-row"><span class="price">$12.00</span><span class="shop">SHOP NOW</span></div>
    </article>
    <article class="abs product" style="left:701px">
      <div class="product-photo" role="img" aria-label="Olive oil soap bar with lavender sprigs and olives" style="background:linear-gradient(160deg,#9a8ab8,#e6d9bf 35%,#d9c49b 65%,#6f8a45)"></div>
      <div class="product-name">Sandalwood</div>
      <div class="product-row"><span class="price">$12.00</span><span class="shop">SHOP NOW</span></div>
    </article>
  </section>

  <footer>
    <div class="abs footer"></div>
    <div class="abs news-label">Sign up Newsletter</div>
    <div class="abs email">Enter your email</div>
    <div class="abs subscribe">SUBSCRIBE</div>
    <div class="abs social" style="left:534px"><i></i>Join us on Flocker</div>
    <div class="abs social" style="right:117px"><i style="background:var(--social-alt)"></i>Join us on Chirper</div>

    <div class="abs col" style="left:117px"><h4>Customer Services</h4>
      <ul><li style="width:117px">FAQ<br>Contact us<br>Order traking</li><li>Shipping &amp; Returns<br>Help<br>100% Guaranteed</li></ul></div>
    <div class="abs col" style="left:385px"><h4>Useful Links</h4>
      <ul><li style="width:81px">Home<br>Soaps<br>Bodybutter</li><li>Two by two<br>Skin facts<br>About</li></ul></div>
    <div class="abs col" style="left:597px"><h4>Help &amp; Info</h4>
      <ul><li>Customer services<br>Blog<br>Sitemap<br>Search terms</li></ul></div>
    <div class="abs col" style="right:117px;text-align:right"><h4>Payment Methods</h4></div>
    <div class="abs cards"><span>Paylo</span><span>Cardex</span><span>Vanta</span><span>Amerex</span></div>

    <div class="abs copy">Copyright @ Brevin Organics. All rights reserved.</div>
    <div class="abs legal">Term of use | Privacy Policy</div>
  </footer>
</div>
</body>
</html>
```